Brand new letterhead, business card, email signature etc.

We are a financial company in London, UK. Our website is www.marlowvane.com. We're wanting a complete remodel of the company colours, letter head, business cards, email signatures, etc. Looking to keep the same font for the company name. I have upload a colour palette that we want to work with. We're looking for company letterhead for outgoing letters/ correspondence, letterhead for internal documentation, email signatures, e-letters. etc. Ultimately we will redesign the entire website also. It is important that our clients get a strong, secure, warm, trustworthy, solid feeling and first impression.
Updates

Designs look the same

Target Market(s)

Institutional investors, (ultra) high net worth individuals

Industry/Entity Type

Finance, Invesments banking.

Font styles to use
Other font styles liked:
• Current font is "Champagne & Limousines"

Requirements
Must have
• Must use the colours provided on the PDF uploaded to the portal. The purple = main colour. The red = accent colour.
Nice to have
• Nice to use same font as now for the company name "Corvane". Font is "Champagne & Limousines". Nice to have some reference to the old logo flower, but only subtle.
Should not have
• Do not use the colour red from our website. Use the colours provided on the colour palette PDF that I uploaded in the portal.

```html
<!DOCTYPE html>
<html lang="en">
<head>
<meta charset="utf-8">
<title>Corvane Business Card</title>
<link href="https://fonts.googleapis.com/css2?family=Jost:wght@300;400;700&display=swap" rel="stylesheet">
<style>
  :root {
    --backdrop: #1c1524;
    --card: #2d1a45;
    --card-emboss: #3d2660;
    --emboss-shadow: #1a0d2b;
    --accent: #d6283a;
    --ink: #ffffff;
    --deco-light: #3a2358;
    --deco-dark: #2f1c48;
  }
  * { margin: 0; padding: 0; box-sizing: border-box; }
  html, body {
    width: 1200px; height: 780px; overflow: hidden;
    background: var(--backdrop);
    font-family: "Jost", sans-serif;
  }
  .sheet {
    width: 1200px; height: 780px;
    display: flex; flex-direction: column;
    align-items: center; justify-content: center; gap: 40px;
  }
  .card {
    position: relative;
    width: 580px; height: 331px;
    background: var(--card);
    border-bottom: 4px solid var(--accent);
    box-shadow: 0 14px 30px rgba(0,0,0,.45);
    overflow: hidden;
  }

  /* wordmark */
  .brand { position: absolute; display: flex; align-items: center; }
  .brand-square { border: 1px solid currentColor; flex: none; }
  .brand-name { font-weight: 300; text-transform: uppercase; line-height: 1; }

  /* back side */
  .card--back .brand {
    left: 50%; top: 50%; transform: translate(-50%, -50%);
    color: var(--card-emboss);
    text-shadow: 1px 1px 0 var(--emboss-shadow);
  }
  .card--back .brand-square {
    width: 70px; height: 70px; margin-right: 26px;
    border-width: 2px;
    box-shadow: 1px 1px 0 var(--emboss-shadow);
  }
  .card--back .brand-name { font-size: 46px; letter-spacing: .28em; }

  /* front side */
  .card--front .brand { left: 34px; top: 40px; color: var(--ink); }
  .card--front .brand-square { width: 58px; height: 58px; margin-right: 20px; }
  .card--front .brand-name { font-size: 30px; letter-spacing: .3em; }

  .decoration {
    position: absolute; right: 22px; top: 22px;
    width: 230px; height: 205px;
    border-radius: 6px;
    background: radial-gradient(ellipse at 55% 45%, var(--deco-light), var(--deco-dark) 75%);
  }

  .details { position: absolute; left: 34px; bottom: 22px; right: 24px; color: var(--ink); }
  .person { font-size: 27px; font-weight: 700; line-height: 1; margin-bottom: 14px; }
  .person-first { color: var(--accent); }
  .person-role { color: var(--accent); font-weight: 300; font-size: 19px; margin-left: 6px; }
  .contact-row { display: flex; gap: 26px; font-size: 13.5px; font-weight: 400; margin-bottom: 6px; }
  .label { color: var(--accent); font-weight: 300; margin-right: 3px; }
  .address { font-size: 13.5px; font-weight: 400; }
</style>
</head>
<body>
<main class="sheet">

  <section class="card card--back" aria-label="Card back">
    <div class="brand">
      <span class="brand-square"></span>
      <span class="brand-name">Corvane</span>
    </div>
  </section>

  <section class="card card--front" aria-label="Card front">
    <div class="decoration" role="img" aria-label="Large embossed blind-pressed flower decoration"></div>

    <div class="brand">
      <span class="brand-square"></span>
      <span class="brand-name">Corvane</span>
    </div>

    <div class="details">
      <p class="person">
        <span class="person-first">Elena</span> <span class="person-last">Marsh</span><span class="person-role">CEO</span>
      </p>
      <p class="contact-row">
        <span><span class="label">T:</span>(020) 7946-0318</span>
        <span><span class="label">E:</span>info@marlowvane.com</span>
        <span><span class="label">W:</span>www.marlowvane.com</span>
      </p>
      <p class="address">48 Aldgate Row, Suite 300 London, EC3N 1AL</p>
    </div>
  </section>

</main>
</body>
</html>
```